Christian Media Company Website

I am looking to design an easy to follow, sleek, creative website for my Christian video Bible study platform. On this platform you will be able to sign up to have access to dozens of free high-quality video Bible studies. With that being said There will be a total of 3 pages needed.

First, I will need the home page. This should contain all critical information to inform the customer. The design should be easy to follow, professional, and creative. I will post to some websites I like, if you just copy the website in your design will be removed immediately.

Secondly, we will need a landing Bible study page for people to look through the Bible studies to select one. I have uploaded Study images below with the aspect ratio I want for the design (for each Bible study image). There should be 2 sections Topical studies and Doctrinal Studies (with series under each section). I would like for people to be able to slide left or right through the studies under each category.

Lastly, we will need a video series page. This page needs to have the video they are watching, a playlist of the other videos, as well as a place to put the speaker's image and description. We will have studies that they can download so please make a place for this.

I will upload our color in the files along with our logo! Looking forward to seeing what you all will come up with!

Websites I like :
https://lanternvale.org/
https://www.quillharborfilms.org/
https://www.dunmorel.com/
https://tessavint.org/

Target Market(s)

Christians

Industry/Entity Type

Christian Video Design

Coding

Coded - Design and coding required

Number of Pages Required

3 page

Font styles to use
Sans Serif

Colors
00AB8E
00BBA5
67D7C9
C6EFE9
E9F9F6

Requirements
Should not have
• Pre-Used Templates

```html
<!DOCTYPE html>
<html lang="en">
<head>
<meta charset="utf-8">
<title>Lampstand Project – Home</title>
<link href="https://fonts.googleapis.com/css2?family=Poppins:wght@400;500;600;700;800&display=swap" rel="stylesheet">
<style>
:root{
  --teal-dark:#00AB8E;
  --teal:#00BBA5;
  --teal-soft:#67D7C9;
  --teal-pale:#C6EFE9;
  --teal-mist:#E9F9F6;
  --ink:#2b2b2b;
  --body:#444;
  --white:#fff;
}
*{box-sizing:border-box;margin:0;padding:0}
html,body{width:1200px;height:3420px;overflow:hidden}
body{font-family:'Poppins',sans-serif;color:var(--ink);background:var(--white);position:relative}
.abs{position:absolute}
.btn{position:absolute;display:flex;align-items:center;justify-content:center;gap:12px;background:var(--teal-dark);color:var(--white);font-weight:700;font-size:18px;border-radius:40px;text-transform:uppercase;letter-spacing:.3px}

/* header */
.site-header{position:absolute;left:0;top:0;width:1200px;height:111px;background:var(--white)}
.brand{position:absolute;display:flex;align-items:center;gap:12px;color:var(--teal);font-weight:700;line-height:1.05;text-transform:uppercase}
.brand-mark{border:4px solid var(--teal);border-radius:2px}
.site-header .brand{left:74px;top:27px;font-size:27px}
.site-header .brand-mark{width:74px;height:50px}
.main-nav{position:absolute;top:48px;left:0;font-size:15px;font-weight:500;text-transform:uppercase}
.main-nav a{position:absolute;white-space:nowrap;color:var(--ink);text-decoration:none}
.main-nav .active{color:var(--teal)}
.login{left:1008px;top:37px;width:119px;height:40px;font-size:15px;font-weight:600}

/* hero */
.hero{position:absolute;left:0;top:111px;width:1200px;height:709px;background:linear-gradient(110deg,#3a3f4a 0%,#6f6a5e 35%,#a9a290 55%,#7c7566 75%,#3d3a33 100%)}
.hero-frame{left:705px;top:197px;width:420px;height:314px;border:4px solid var(--teal)}
.hero-title{right:103px;top:250px;font-size:53px;font-weight:800;color:var(--white);text-align:right;text-transform:uppercase;white-space:nowrap}
.hero-sub{right:103px;top:322px;font-size:32px;font-weight:700;color:var(--white);text-align:right;line-height:44px;text-transform:uppercase}
.watch{left:74px;top:615px;width:199px;height:45px;border:2px solid var(--white);border-radius:30px;color:var(--white);font-size:15px;font-weight:600;display:flex;align-items:center;justify-content:center;gap:14px}
.hero-arrows{left:1058px;top:628px}

/* about */
h2.section-title{position:absolute;left:0;width:1200px;text-align:center;font-size:38px;font-weight:800;text-transform:uppercase}
.about-copy{left:90px;top:960px;width:1020px;text-align:center;font-size:18px;line-height:35px;color:var(--body)}

/* speakers */
.speakers{position:absolute;left:0;top:1285px;width:1200px;height:719px;background:var(--teal-mist)}
.card{position:absolute;top:142px;width:329px;height:477px;background:var(--white)}
.card.featured{box-shadow:0 4px 14px rgba(0,0,0,.15)}
.card-media{position:absolute;left:16px;top:14px;width:297px;height:271px;display:flex;align-items:center;justify-content:center}
.card h3{position:absolute;top:310px;width:100%;text-align:center;color:var(--teal-dark);font-size:24px;font-weight:800;text-transform:uppercase}
.card p{position:absolute;top:348px;left:20px;right:20px;text-align:center;font-size:17.5px;line-height:28px;color:var(--body)}
.card .btn{left:60px;top:444px;width:208px;height:66px}
.chevron{position:absolute;top:385px}

/* studies */
.study-img{position:absolute}
.study-title{position:absolute;font-size:38px;font-weight:800;text-transform:uppercase}
.study-copy{position:absolute;width:510px;font-size:17.5px;line-height:35px;color:var(--body)}

/* footer */
.site-footer{position:absolute;left:0;top:3032px;width:1200px;height:388px;background:var(--teal-pale)}
.signup{left:74px;top:36px;width:513px;height:313px;background:var(--teal-soft);border-radius:27px}
.signup-tail{left:586px;top:160px}
.signup h2{position:absolute;left:25px;top:30px;color:var(--white);font-size:38px;font-weight:800;text-transform:uppercase}
.signup p{position:absolute;left:25px;top:88px;width:460px;color:var(--white);font-size:17.5px;line-height:31px}
.signup-field{left:25px;top:169px;width:460px;height:66px;background:var(--white);border-radius:40px;display:flex;align-items:center;justify-content:space-between;padding:0 24px}
.signup-field span{font-size:17px;color:var(--body)}
.signup-field strong{color:var(--teal-dark);font-size:17px;font-weight:700}
.site-footer .brand{left:880px;top:86px;font-size:26px}
.site-footer .brand-mark{width:72px;height:52px}
.copyright{right:73px;top:182px;text-align:right;font-size:17.5px;line-height:31px;color:var(--ink)}
.social{left:890px;top:268px;display:flex;gap:34px}
.social span{width:24px;height:24px;border-radius:50%;background:var(--teal-dark);display:block}
</style>
</head>
<body>

<header class="site-header">
  <div class="brand"><span class="brand-mark"></span><span>Lampstand<br>Project</span></div>
  <nav class="main-nav">
    <a class="active" style="left:418px">Home</a>
    <a style="left:498px">About Us</a>
    <a style="left:609px">Bible Series</a>
    <a style="left:737px">Our Speakers</a>
    <a style="left:884px">Contact Us</a>
  </nav>
  <a class="btn login">Log In</a>
</header>

<section class="hero" role="img" aria-label="Photo of an older woman with headphones speaking on a video call at her laptop, a Bible on the table">
  <div class="abs hero-frame"></div>
  <h1 class="abs hero-title">Lampstand Project</h1>
  <p class="abs hero-sub">Sed ut perspiciatis unde<br>omnis iste natus error sit<br>accusantium dolo</p>
  <div class="abs watch">
    <svg width="16" height="16" viewBox="0 0 16 16"><circle cx="8" cy="8" r="6.5" fill="none" stroke="#fff" stroke-width="1.5"/><path d="M6.5 5v6l4.5-3z" fill="#fff"/></svg>
    WATCH VIDEO
  </div>
  <svg class="abs hero-arrows" width="72" height="20" viewBox="0 0 72 20">
    <path d="M22 10H4M10 4L4 10l6 6" stroke="#fff" stroke-width="3" fill="none"/>
    <path d="M48 10h18M60 4l6 6-6 6" stroke="#fff" stroke-width="3" fill="none"/>
  </svg>
</section>

<h2 class="section-title" style="top:896px">About Lampstand Project</h2>
<p class="abs about-copy">Sed ut perspiciatis unde omnis iste natus error sit voluptatem accusantium doloremque laudantium, totam rem aperiam, eaque ipsa quae ab illo inventore veritatis et quasi architecto beatae vitae dicta sunt explicaboemo enim ipsam voluptatem quia voluptas sit aspernatur aut odit aut fugit, sed quia consequuntur magni dolores eos qui ratione voluptatem sequi nesciunt.</p>
<a class="btn" style="left:496px;top:1133px;width:207px;height:67px">Read More</a>

<section class="speakers">
  <h2 class="section-title" style="top:58px">Speaker's Video</h2>
  <svg class="chevron" style="left:40px" width="22" height="34" viewBox="0 0 22 34"><path d="M18 2L4 17l14 15" stroke="#333" stroke-width="2.5" fill="none"/></svg>
  <svg class="chevron" style="left:1140px" width="22" height="34" viewBox="0 0 22 34"><path d="M4 2l14 15L4 32" stroke="#333" stroke-width="2.5" fill="none"/></svg>

  <article class="card featured" style="left:74px">
    <div class="card-media" role="img" aria-label="Portrait of a smiling woman outdoors" style="background:linear-gradient(135deg,#8c9a72,#5d6b4a 55%,#2c2c30)">
      <svg width="48" height="48" viewBox="0 0 48 48"><circle cx="24" cy="24" r="21" fill="none" stroke="#fff" stroke-width="3"/><path d="M19 14v20l16-10z" fill="#fff"/></svg>
    </div>
    <h3>All The Things</h3>
    <p>Sed ut perspiciatis unde omnis iste natus error sit voluptat aliquip exmmodo</p>
    <a class="btn"><svg width="18" height="18" viewBox="0 0 18 18"><path d="M9 1v10M4 7l5 5 5-5M1 16h16" stroke="#fff" stroke-width="2.5" fill="none"/></svg>Download</a>
  </article>

  <article class="card" style="left:437px">
    <div class="card-media" role="img" aria-label="Man seen from behind looking over a hilly landscape" style="background:linear-gradient(135deg,#c9c5bc,#9d9a8d 50%,#5b5d5e)">
      <svg width="48" height="48" viewBox="0 0 48 48"><circle cx="24" cy="24" r="21" fill="none" stroke="#fff" stroke-width="3"/><path d="M19 14v20l16-10z" fill="#fff"/></svg>
    </div>
    <h3>God's Design</h3>
    <p>Sed ut perspiciatis unde omnis iste natus error sit voluptat aliquip exmmodo</p>
    <a class="btn"><svg width="18" height="18" viewBox="0 0 18 18"><path d="M9 1v10M4 7l5 5 5-5M1 16h16" stroke="#fff" stroke-width="2.5" fill="none"/></svg>Download</a>
  </article>

  <article class="card" style="left:798px">
    <div class="card-media" role="img" aria-label="Portrait of an older man in a pink shirt in a wooded garden" style="background:linear-gradient(135deg,#4f5e3a,#8a7a60 50%,#d88c80)">
      <svg width="48" height="48" viewBox="0 0 48 48"><circle cx="24" cy="24" r="21" fill="none" stroke="#fff" stroke-width="3"/><path d="M19 14v20l16-10z" fill="#fff"/></svg>
    </div>
    <h3>Revival</h3>
    <p>Sed ut perspiciatis unde omnis iste natus error sit voluptat aliquip exmmodo</p>
    <a class="btn"><svg width="18" height="18" viewBox="0 0 18 18"><path d="M9 1v10M4 7l5 5 5-5M1 16h16" stroke="#fff" stroke-width="2.5" fill="none"/></svg>Download</a>
  </article>
</section>

<div class="study-img" role="img" aria-label="Two men sitting outdoors reading an open Bible together" style="left:74px;top:2077px;width:526px;height:442px;border-top-left-radius:140px;background:linear-gradient(120deg,#4a5a3a,#b23a3a 50%,#6a2a2a 80%,#3a2a22)"></div>
<h2 class="study-title" style="left:624px;top:2138px">Topical Studies</h2>
<p class="study-copy" style="left:624px;top:2206px">Sed ut perspiciatis unde omnis iste natus error sit voluptatem accusantium doloremque laudantium, totam rem&nbsp; aperiam, eaque ipsa quae ab illo inventore veritatis et quasi architecto beatae vitae dicta.</p>
<a class="btn" style="left:624px;top:2378px;width:207px;height:66px">Read More</a>

<div class="study-img" role="img" aria-label="Young woman in a scarf reading a book on a bench among autumn trees" style="left:600px;top:2519px;width:527px;height:441px;border-top-right-radius:140px;background:linear-gradient(135deg,#d8b23a,#b88a2a 40%,#e9d89a 65%,#6a5a3a)"></div>
<h2 class="study-title" style="left:74px;top:2580px">Doctrinal Studies</h2>
<p class="study-copy" style="left:74px;top:2648px">Sed ut perspiciatis unde omnis iste natus error sit voluptatem accusantium doloremque laudantium, totam rem&nbsp; aperiam, eaque ipsa quae ab illo inventore veritatis et quasi architecto beatae vitae dicta.</p>
<a class="btn" style="left:74px;top:2820px;width:207px;height:66px">Read More</a>

<footer class="site-footer">
  <svg class="abs signup-tail" width="40" height="80" viewBox="0 0 40 80"><path d="M0 0L38 35 0 78z" fill="#67D7C9"/></svg>
  <div class="abs signup">
    <h2>Email Sign Up</h2>
    <p>Sed ut perspiciatis unde omnis iste natus error sit voluptatem accusantium doloremque.</p>
    <div class="abs signup-field"><span>Email Address</span><strong>SIGN UP →</strong></div>
  </div>
  <div class="brand"><span class="brand-mark"></span><span>Lampstand<br>Project</span></div>
  <p class="abs copyright">Copyright © 2022 CompanyName<br>All Rights Reserved</p>
  <div class="abs social" aria-label="Social media links"><span></span><span></span><span></span><span></span><span></span></div>
</footer>

</body>
</html>
```